Veltrane Group Business Card Design

The CEO is looking for a new trendy look for his business card.
You can stay with current branding or come up with something new/creative. It can be 3D, including Medical Office buildings. You can use our logo in a variety of colors. Please include name, title, company name, company website, email address, cell number

Target Market(s)

Real Estate Development and Construction

Industry/Entity Type

Health care real estate

Contact Information for Business Card

Rohesh Kamdar, CEO M-604.781.2249 E-roheshkamdar@veltrane.com Address:4180 Lindqvist Ave, Tampa, FL 33482 www.veltrane.com

Font styles to use
Other font styles liked:
• Be creative

Requirements
Must have
• Creative, trendy look
Nice to have
• Please go to our website to get a feel- www. veltrane.com
Should not have
• small fonts

```html
<!DOCTYPE html>
<html lang="en">
<head>
<meta charset="UTF-8">
<title>Veltrane Group – Business Card</title>
<link href="https://fonts.googleapis.com/css2?family=Libre+Baskerville:wght@700&family=Open+Sans:wght@400;700;800&display=swap" rel="stylesheet">
<style>
  :root {
    --bg: #e9e6e1;
    --dark: #2c2c2e;
    --dark-deep: #222224;
    --red: #a81c2a;
    --navy: #1b2d54;
    --paper: #ffffff;
    --paper-shade: #ececec;
    --ink: #3a3a3a;
  }
  * { box-sizing: border-box; margin: 0; padding: 0; }
  html, body { width: 1200px; height: 900px; overflow: hidden; }
  body {
    background: var(--bg);
    font-family: "Open Sans", sans-serif;
    position: relative;
  }
  .card {
    position: absolute;
    left: 250px;
    width: 700px;
    height: 400px;
    overflow: hidden;
    box-shadow: 0 10px 28px rgba(0,0,0,.25);
  }
  /* Back side */
  .card--back {
    top: 40px;
    background: linear-gradient(135deg, #363638 0%, var(--dark) 50%, var(--dark-deep) 100%);
  }
  .card--back .brand-emboss {
    position: absolute;
    right: 90px;
    top: 120px;
    font-family: "Open Sans", sans-serif;
    font-weight: 800;
    font-size: 70px;
    letter-spacing: -2px;
    color: #262628;
    line-height: 1;
  }
  .back-stripe {
    position: absolute;
    left: 0; right: 0; bottom: 0;
    height: 20px;
    background: var(--red);
  }
  .back-web {
    position: absolute;
    left: 0; bottom: 0;
    width: 340px;
    height: 56px;
    background: var(--navy);
    clip-path: polygon(0 0, 88% 0, 100% 100%, 0 100%);
    color: #fff;
    font-weight: 700;
    font-size: 20px;
    letter-spacing: .5px;
    padding: 14px 0 0 34px;
  }
  /* Front side */
  .card--front {
    top: 470px;
    background: linear-gradient(120deg, var(--paper-shade) 0%, var(--paper) 45%, var(--paper-shade) 80%, var(--paper) 100%);
  }
  .brand {
    position: absolute;
    right: 56px;
    top: 52px;
    font-family: "Open Sans", sans-serif;
    font-weight: 800;
    font-size: 64px;
    letter-spacing: -2px;
    color: var(--red);
    line-height: 1;
  }
  .divider {
    position: absolute;
    left: 180px;
    right: 40px;
    top: 222px;
    height: 1.5px;
    background: var(--red);
  }
  .person { position: absolute; left: 56px; top: 178px; }
  .person__name {
    font-family: "Libre Baskerville", serif;
    font-weight: 700;
    font-size: 26px;
    color: var(--navy);
  }
  .person__title {
    font-weight: 700;
    font-size: 18px;
    color: var(--red);
    margin-top: 2px;
  }
  .contacts {
    position: absolute;
    left: 56px;
    top: 262px;
    list-style: none;
    font-size: 17px;
    color: var(--ink);
  }
  .contacts li { display: flex; align-items: center; gap: 12px; height: 28px; }
  .contacts svg { width: 18px; height: 18px; flex: none; }
  .front-stripe {
    position: absolute;
    left: 0; bottom: 0;
    width: 460px;
    height: 22px;
    background: var(--red);
  }
  .front-web {
    position: absolute;
    right: 0; bottom: 0;
    width: 270px;
    height: 72px;
    background: var(--navy);
    clip-path: polygon(0 0, 100% 0, 100% 100%, 6% 100%);
    color: #fff;
    font-weight: 700;
    font-size: 20px;
    letter-spacing: .5px;
    padding: 22px 0 0 46px;
  }
</style>
</head>
<body>
  <section class="card card--back" aria-label="Business card back">
    <div class="brand-emboss">Veltrane Group</div>
    <div class="back-stripe"></div>
    <div class="back-web">www.veltrane.com</div>
  </section>

  <section class="card card--front" aria-label="Business card front">
    <div class="brand">Veltrane Group</div>
    <div class="divider"></div>
    <div class="person">
      <div class="person__name">Rohesh Kamdar</div>
      <div class="person__title">CEO</div>
    </div>
    <ul class="contacts">
      <li>
        <svg viewBox="0 0 18 18" aria-hidden="true"><rect x="5" y="1.5" width="8" height="15" rx="1.5" fill="none" stroke="#1b2d54" stroke-width="1.6"/><line x1="8" y1="14" x2="10" y2="14" stroke="#1b2d54" stroke-width="1.4"/></svg>
        604.781.2249
      </li>
      <li>
        <svg viewBox="0 0 18 18" aria-hidden="true"><rect x="1.5" y="4" width="15" height="10" fill="#1b2d54"/><polyline points="1.5,4 9,10 16.5,4" fill="none" stroke="#fff" stroke-width="1.3"/></svg>
        roheshkamdar@veltrane.com
      </li>
      <li>
        <svg viewBox="0 0 18 18" aria-hidden="true"><path d="M9 17 C9 17 3.5 10.5 3.5 7 A5.5 5.5 0 0 1 14.5 7 C14.5 10.5 9 17 9 17 Z" fill="#1b2d54"/><circle cx="9" cy="7" r="2.2" fill="#fff"/></svg>
        4180 Lindqvist Ave, Tampa, FL 33482
      </li>
    </ul>
    <div class="front-stripe"></div>
    <div class="front-web">www.veltrane.com</div>
  </section>
</body>
</html>
```